Business Card Design - Property Management & Real Estate Services

I need a business card design for my company that I can print ZEPLA Cards. The company is called Brindle Management Company. It is a property management and real estate company. The design has to be clean and modern. I need two versions. One for my employee and one for me. However, the design will be the same, just different text. You can get a feel for the company by looking at our website at www.brindlemanagement.example.

Industry/Entity Type

Property Management

Contact Information for Business Card

I will be using ZEPLA.com to print my cards. I will most likely use the rounded edges card. I need two versions, however, they will be the same design. I need one for me and my employee.

Colors
3276b5
33a6d7

Requirements
Must have
• Company Logo
• Name of person
• Property Management & Real Estate Service
• Phone
• Email
• Website
• Address
• A space to place a QR code

```html
<!DOCTYPE html>
<html lang="en">
<head>
<meta charset="utf-8">
<title>Brindle Management – Business Cards</title>
<link href="https://fonts.googleapis.com/css2?family=Roboto:wght@400;500&family=Roboto+Condensed:wght@700&display=swap" rel="stylesheet">
<style>
  :root {
    --bg: #c9c9c9;
    --card: #fbfbfb;
    --navy: #1d4f9e;
    --sky: #6a9ad4;
    --text: #3a3a3a;
    --muted: #555;
  }
  * { margin: 0; padding: 0; box-sizing: border-box; }
  html, body { width: 1200px; height: 852px; overflow: hidden; background: var(--bg); }
  .stage {
    width: 1200px; height: 852px;
    display: flex; align-items: center; justify-content: center; gap: 40px;
  }
  .card {
    position: relative; width: 540px; height: 310px;
    background: var(--card); border-radius: 18px; overflow: hidden;
    box-shadow: 0 4px 14px rgba(0,0,0,.18);
    font-family: "Roboto", sans-serif; color: var(--text);
  }
  .card-bands { position: absolute; left: 0; bottom: 0; width: 540px; height: 70px; }
  .wordmark {
    display: flex; align-items: center; gap: 12px;
    font-family: "Roboto", sans-serif; font-weight: 500; color: var(--navy);
    letter-spacing: .5px; white-space: nowrap;
  }
  .wordmark-square { width: 18px; height: 18px; background: var(--sky); flex: none; }

  /* front */
  .card-front .wordmark { position: absolute; top: 100px; left: 0; right: 0; justify-content: center; font-size: 38px; }
  .front-url {
    position: absolute; top: 196px; left: 0; right: 0;
    display: flex; align-items: center; justify-content: center; gap: 14px;
    font-size: 15px; color: var(--text);
  }
  .front-url .rule { width: 60px; height: 2px; background: var(--navy); }

  /* back */
  .card-back .wordmark { position: absolute; top: 48px; left: 38px; font-size: 30px; }
  .person { position: absolute; left: 38px; top: 150px; }
  .person-name { font-family: "Roboto Condensed", sans-serif; font-weight: 700; font-size: 25px; color: var(--navy); white-space: nowrap; }
  .person-title { font-size: 15px; color: var(--muted); margin-top: 4px; }
  .address { position: absolute; left: 38px; top: 214px; font-size: 15px; line-height: 21px; color: var(--text); white-space: nowrap; }
  .contact { position: absolute; left: 262px; top: 112px; list-style: none; font-size: 13px; line-height: 22px; white-space: nowrap; }
  .contact li { display: flex; align-items: center; gap: 8px; }
  .contact svg { width: 12px; height: 12px; fill: var(--navy); flex: none; }
  .tagline {
    position: absolute; right: 0; bottom: 14px; width: 314px; height: 42px;
    display: flex; align-items: center; justify-content: center;
    font-size: 11.5px; font-weight: 500; color: #fff; white-space: nowrap;
  }
</style>
</head>
<body>
<main class="stage">
  <section class="card card-front" aria-label="Card front">
    <div class="wordmark"><span class="wordmark-square"></span>Brindle Management</div>
    <div class="front-url"><span class="rule"></span>www.brindlemanagement.example<span class="rule"></span></div>
    <svg class="card-bands" viewBox="0 0 540 70" aria-hidden="true">
      <path d="M0 58 H540 V70 H0 Z" fill="var(--sky)"/>
      <path d="M290 58 L300 48 H540 V58 Z" fill="var(--navy)"/>
    </svg>
  </section>

  <section class="card card-back" aria-label="Card back">
    <div class="wordmark"><span class="wordmark-square"></span>Brindle Management</div>
    <div class="person">
      <div class="person-name">Dario M. Castell</div>
      <div class="person-title">Founder</div>
    </div>
    <div class="address">480 Harbor Lane<br>#210 Miami, FL 33130</div>
    <ul class="contact">
      <li><svg viewBox="0 0 12 12"><path d="M2 1h2l1 3-1.4 1a7 7 0 0 0 3.4 3.4L8 7l3 1v2a1 1 0 0 1-1 1A9 9 0 0 1 1 2a1 1 0 0 1 1-1z"/></svg>(305) 555-0142</li>
      <li><svg viewBox="0 0 12 12"><path d="M1 2h10v8H1z M1 2l5 4 5-4" fill="none" stroke="var(--navy)" stroke-width="1.4"/></svg>dario@brindlemanagement.example</li>
      <li><svg viewBox="0 0 12 12"><circle cx="6" cy="6" r="5" fill="none" stroke="var(--navy)" stroke-width="1.2"/><path d="M1 6h10M6 1c-3 3-3 7 0 10M6 1c3 3 3 7 0 10" fill="none" stroke="var(--navy)" stroke-width="1"/></svg>www.brindlemanagement.example</li>
    </ul>
    <svg class="card-bands" viewBox="0 0 540 70" aria-hidden="true">
      <path d="M0 56 H540 V70 H0 Z" fill="var(--sky)"/>
      <path d="M226 56 V28 Q226 14 242 14 H540 V56 Z" fill="var(--navy)"/>
    </svg>
    <div class="tagline">Miami Property Management &amp; Real Estate Services</div>
  </section>
</main>
</body>
</html>
```